Business Card Design

I already have a company logo for my company. I have a logo for the manufacturer we represent. I want a professional business card design.

```html
<!DOCTYPE html>
<html lang="en">
<head>
<meta charset="utf-8">
<title>Beacon Signal Co. – Business Card</title>
<link href="https://fonts.googleapis.com/css2?family=Open+Sans:wght@400;600;700&display=swap" rel="stylesheet">
<style>
  :root {
    --backdrop: #222224;
    --card: #1f1f22;
    --card-edge: #2a2a2e;
    --pattern-light: #2e2e33;
    --pattern-dark: #19191c;
    --white: #f2f2f2;
    --soft-white: #d9d9dc;
    --red: #e8262b;
    --gold: #d4a22a;
    --rule: #8a8a8f;
  }
  * { box-sizing: border-box; margin: 0; padding: 0; }
  html, body {
    width: 1200px; height: 780px; overflow: hidden;
    background: var(--backdrop);
    font-family: "Open Sans", Arial, sans-serif;
  }
  .canvas {
    width: 1200px; height: 780px;
    display: flex; align-items: center; justify-content: center; gap: 40px;
  }
  .card {
    position: relative;
    width: 560px; height: 320px;
    background: var(--card);
    border: 1px solid var(--card-edge);
    border-radius: 4px;
    box-shadow: 0 18px 40px rgba(0,0,0,.55);
    overflow: hidden;
  }

  /* Brand name block (stands in for the company mark) */
  .brand {
    display: flex; align-items: center; gap: 12px;
  }
  .brand-square {
    width: 26px; height: 26px; background: var(--red); flex: none;
  }
  .brand-name {
    color: var(--white); font-weight: 700; line-height: 1.05;
    letter-spacing: .5px; text-transform: uppercase;
  }

  /* Front */
  .card-front .brand {
    position: absolute; left: 44px; top: 70px;
  }
  .card-front .brand-name { font-size: 26px; }
  .divider {
    position: absolute; left: 282px; top: 58px;
    width: 1px; height: 150px; background: var(--rule);
  }
  .contact-block {
    position: absolute; left: 312px; top: 56px;
  }
  .person-name {
    font-size: 34px; font-weight: 700; line-height: 1.1; white-space: nowrap;
  }
  .person-name .first { color: var(--red); }
  .person-name .last { color: var(--gold); }
  .person-title {
    color: var(--white); font-size: 17px; font-weight: 600; margin-top: 2px;
  }
  .contact-list { list-style: none; margin-top: 16px; }
  .contact-list li {
    display: flex; align-items: center; gap: 10px;
    color: var(--soft-white); font-size: 16px; line-height: 1.6;
  }
  .contact-list svg { width: 14px; height: 14px; flex: none; fill: var(--red); }
  .address {
    position: absolute; left: 44px; bottom: 34px;
    color: var(--soft-white); font-size: 15px; letter-spacing: .2px;
  }

  /* Back */
  .card-back .pattern {
    position: absolute; inset: 0;
    background: linear-gradient(135deg, var(--pattern-dark) 0%, var(--pattern-light) 55%, var(--pattern-dark) 100%);
  }
  .card-back .brand {
    position: absolute; left: 50%; top: 50%; transform: translate(-50%, -50%);
  }
  .card-back .brand-square { width: 34px; height: 34px; }
  .card-back .brand-name { font-size: 36px; }
</style>
</head>
<body>
<main class="canvas">

  <section class="card card-front" aria-label="Card front">
    <div class="brand">
      <span class="brand-square"></span>
      <span class="brand-name">Beacon<br>Signal Co.</span>
    </div>

    <span class="divider"></span>

    <div class="contact-block">
      <h1 class="person-name"><span class="first">Tomas</span> <span class="last">Varek</span></h1>
      <p class="person-title">Managing Director</p>
      <ul class="contact-list">
        <li>
          <svg viewBox="0 0 24 24" aria-hidden="true"><path d="M6.6 10.8a15.1 15.1 0 0 0 6.6 6.6l2.2-2.2a1 1 0 0 1 1-.25 11.4 11.4 0 0 0 3.6.57 1 1 0 0 1 1 1V20a1 1 0 0 1-1 1A17 17 0 0 1 3 4a1 1 0 0 1 1-1h3.5a1 1 0 0 1 1 1c0 1.25.2 2.45.57 3.57a1 1 0 0 1-.25 1z"/></svg>
          (555) 014-2290
        </li>
        <li>
          <svg viewBox="0 0 24 24" aria-hidden="true"><path d="M2 5h20v14H2zm2 2v.5l8 5 8-5V7zm0 2.8V17h16V9.8l-8 5z"/></svg>
          info@beaconsignal.com
        </li>
        <li>
          <svg viewBox="0 0 24 24" aria-hidden="true"><path d="M12 2a10 10 0 1 0 0 20 10 10 0 0 0 0-20zm6.9 6h-2.9a15.6 15.6 0 0 0-1.4-3.6A8 8 0 0 1 18.9 8zM12 4a14 14 0 0 1 1.9 4h-3.8A14 14 0 0 1 12 4zM4.3 14a8.2 8.2 0 0 1 0-4h3.4a16.5 16.5 0 0 0 0 4zm.8 2H8a15.6 15.6 0 0 0 1.4 3.6A8 8 0 0 1 5.1 16zM8 8H5.1a8 8 0 0 1 4.3-3.6A15.6 15.6 0 0 0 8 8zm4 12a14 14 0 0 1-1.9-4h3.8A14 14 0 0 1 12 20zm2.3-6H9.7a14.7 14.7 0 0 1 0-4h4.6a14.7 14.7 0 0 1 0 4zm.3 5.6A15.6 15.6 0 0 0 16 16h2.9a8 8 0 0 1-4.3 3.6zM16.3 14a16.5 16.5 0 0 0 0-4h3.4a8.2 8.2 0 0 1 0 4z"/></svg>
          www.beaconsignal.com
        </li>
      </ul>
    </div>

    <p class="address">410 Harlow Ave. Suite 120 Dayton, OH 45402</p>
  </section>

  <section class="card card-back" aria-label="Card back">
    <div class="pattern" role="img" aria-label="Faint repeated company mark pattern across the card back"></div>
    <div class="brand">
      <span class="brand-square"></span>
      <span class="brand-name">Beacon<br>Signal Co.</span>
    </div>
  </section>

</main>
</body>
</html>
```